Brindle Barks Chews Pouch Design

I want a pouch design for my yak cheese dog chews. My competitor is kindly tail, see attached. I want something minimalist like that where you see that there is only 3 ingredients, Yak milk, lime juice, Himalayan salt. I want it to say 100% natural 100% organic on it. Also odor free. There has to be a big see through window on it so you can see the products inside. Here is my logo and my competitor package. The package is 13cm x 17cm x 5cm. I have 5 sizes of bags to create but same image design
Updates

Target Market(s)

Pet owners

Industry/Entity Type

Dog products

Requirements
Must have
• « SMALL » « MIN NET WT 200 g / 5 PCS » and its important the 3 ingredients mentioned and 100% natural and organic must be very visible however the window must be big
Should not have
• The ingredients in the back

```html
<!DOCTYPE html>
<html lang="en">
<head>
<meta charset="utf-8">
<title>Brindle Barks Chews – Naturals Pouch</title>
<link rel="stylesheet" href="https://fonts.googleapis.com/css2?family=Kanit:ital,wght@1,800&family=Montserrat:wght@700;800&family=Oswald:wght@300;400;500;600&family=Source+Sans+3:wght@300;700&display=swap">
<style>
  :root {
    --page: #f7f7f6;
    --pouch-light: #e9e9e6;
    --pouch-mid: #dcdcd8;
    --pouch-edge: #c9c9c4;
    --brown: #6b4631;
    --brown-deep: #4e3222;
    --ink: #2a1d16;
    --tan: #d7b894;
    --cream: #f4ede4;
    --chew-a: #e39a3a;
    --chew-b: #c46f1f;
  }
  * { box-sizing: border-box; margin: 0; padding: 0; }
  html, body { width: 1200px; height: 898px; overflow: hidden; background: var(--page); }
  .canvas { position: relative; width: 1200px; height: 898px; }

  .pouch {
    position: absolute; left: 358px; top: 29px; width: 484px; height: 840px;
    background: linear-gradient(90deg, var(--pouch-edge) 0%, var(--pouch-light) 8%, var(--pouch-light) 88%, var(--pouch-mid) 100%);
    border-radius: 26px 26px 34px 34px;
    overflow: hidden;
  }
  .seal { position: absolute; left: 26px; right: 26px; height: 2px; background: var(--pouch-edge); }
  .seal.one { top: 100px; } .seal.two { top: 108px; }

  .claims { position: absolute; top: 36px; left: 0; width: 100%; height: 60px; }
  .claim { position: absolute; width: 60px; text-align: center; }
  .claim svg { display: block; margin: 0 auto; }
  .claim span { display: block; margin-top: 4px; font: 700 5.5px/1 "Montserrat", sans-serif; color: var(--brown); letter-spacing: .2px; }

  .brand-line {
    position: absolute; top: 118px; width: 100%; text-align: center;
    font: 500 26px/1 "Oswald", sans-serif; color: var(--brown-deep); font-variant: small-caps; letter-spacing: .5px;
  }
  .range-name {
    position: absolute; top: 140px; width: 100%; text-align: center;
    font: italic 800 78px/1 "Kanit", sans-serif; color: var(--ink); letter-spacing: -1px;
  }

  .window {
    position: absolute; left: 45px; top: 232px; width: 393px; height: 380px;
    background:
      repeating-linear-gradient(90deg, transparent 0 58px, rgba(120,60,20,.45) 58px 61px),
      linear-gradient(180deg, var(--chew-a), var(--chew-b) 55%, var(--chew-a));
  }

  .odor-tag {
    position: absolute; left: 340px; top: 232px; width: 137px; height: 68px;
    background: var(--brown); display: flex; align-items: center; gap: 8px; padding-left: 12px;
  }
  .odor-tag p { font: 800 21px/0.95 "Montserrat", sans-serif; color: var(--cream); }

  .purity {
    position: absolute; left: 270px; top: 524px; width: 184px; height: 72px;
    background: var(--tan); border-radius: 10px; padding: 8px 0 0 14px;
    transform: rotate(-3deg);
  }
  .purity .natural { font: 300 22px/1.1 "Source Sans 3", sans-serif; color: var(--brown-deep); }
  .purity .organic { font: 700 22px/1.1 "Montserrat", sans-serif; color: var(--ink); letter-spacing: -.3px; }

  .band {
    position: absolute; left: 32px; top: 590px; width: 428px; height: 140px;
    background: var(--brown); clip-path: polygon(0 3%, 100% 0, 100% 97%, 0 100%);
  }

  .brand-mark { position: absolute; left: 58px; top: 492px; width: 130px; text-align: center; }
  .brand-mark .dot { width: 96px; height: 96px; border-radius: 50%; background: var(--tan); margin: 0 auto 8px; }
  .brand-mark .name { font: 600 19px/1.05 "Oswald", sans-serif; color: var(--cream); text-transform: uppercase; }

  .ingredient-count {
    position: absolute; left: 82px; top: 664px; width: 196px; text-align: right;
    font: 400 24px/1 "Oswald", sans-serif; color: var(--cream); white-space: nowrap;
    transform: scaleY(1.25); transform-origin: center;
  }
  .ingredient-count b { font-weight: 500; font-size: 30px; margin: 0 4px; }
  .ingredient-arrow { position: absolute; left: 288px; top: 640px; }

  .ingredients {
    position: absolute; left: 332px; top: 606px; width: 122px; height: 108px;
    border: 1.5px solid var(--cream); border-radius: 14px;
    display: flex; flex-direction: column; justify-content: center; align-items: center; gap: 2px;
  }
  .ingredients li { list-style: none; font: 300 17px/1.2 "Oswald", sans-serif; color: var(--cream); text-transform: uppercase; white-space: nowrap; }

  .net-weight {
    position: absolute; top: 780px; width: 100%; text-align: center;
    font: 800 25px/1 "Montserrat", sans-serif; color: var(--ink);
  }
</style>
</head>
<body>
<main class="canvas">
  <section class="pouch" aria-label="Brindle Barks Chews Naturals pouch front">
    <div class="claims">
      <div class="claim" style="left:80px">
        <svg width="40" height="40" viewBox="0 0 40 40"><circle cx="20" cy="20" r="18" fill="none" stroke="#6b4631" stroke-width="2"/><rect x="15" y="11" width="10" height="18" rx="2" fill="none" stroke="#6b4631" stroke-width="1.6"/><line x1="8" y1="32" x2="32" y2="8" stroke="#6b4631" stroke-width="2"/></svg>
        <span>LACTOSE-FREE</span>
      </div>
      <div class="claim" style="left:134px">
        <svg width="40" height="40" viewBox="0 0 40 40"><circle cx="20" cy="20" r="18" fill="none" stroke="#6b4631" stroke-width="2"/><line x1="20" y1="10" x2="20" y2="30" stroke="#6b4631" stroke-width="1.6"/><ellipse cx="16.5" cy="16" rx="2.5" ry="4" fill="#6b4631"/><ellipse cx="23.5" cy="20" rx="2.5" ry="4" fill="#6b4631"/><line x1="8" y1="32" x2="32" y2="8" stroke="#6b4631" stroke-width="2"/></svg>
        <span>GLUTEN-FREE</span>
      </div>
      <div class="claim" style="left:276px">
        <svg width="40" height="40" viewBox="0 0 40 40"><circle cx="20" cy="20" r="18" fill="none" stroke="#6b4631" stroke-width="2"/><path d="M17 10h6M18 10v7l-6 11h16l-6-11v-7" fill="none" stroke="#6b4631" stroke-width="1.6"/><path d="M14 25l-2 3h16l-2-3z" fill="#6b4631"/><line x1="8" y1="32" x2="32" y2="8" stroke="#6b4631" stroke-width="2"/></svg>
        <span>CHEMICAL-FREE</span>
      </div>
      <div class="claim" style="left:340px">
        <svg width="40" height="40" viewBox="0 0 40 40"><circle cx="20" cy="20" r="18" fill="none" stroke="#6b4631" stroke-width="2"/><line x1="20" y1="9" x2="20" y2="31" stroke="#6b4631" stroke-width="1.6"/><ellipse cx="16.5" cy="15" rx="2.5" ry="3.5" fill="#6b4631"/><ellipse cx="23.5" cy="15" rx="2.5" ry="3.5" fill="#6b4631"/><ellipse cx="16.5" cy="22" rx="2.5" ry="3.5" fill="#6b4631"/><ellipse cx="23.5" cy="22" rx="2.5" ry="3.5" fill="#6b4631"/><line x1="8" y1="32" x2="32" y2="8" stroke="#6b4631" stroke-width="2"/></svg>
        <span>GRAIN-FREE</span>
      </div>
    </div>
    <div class="seal one"></div><div class="seal two"></div>

    <p class="brand-line">Brindle Barks Chews</p>
    <h1 class="range-name">Naturals</h1>

    <div class="window" role="img" aria-label="Clear window showing five golden yak cheese chew sticks"></div>

    <div class="odor-tag">
      <svg width="36" height="36" viewBox="0 0 36 36"><circle cx="18" cy="18" r="16" fill="none" stroke="#f4ede4" stroke-width="1.8"/><path d="M12 26c-3-4 3-6 0-10s3-6 0-8M18 26c-3-4 3-6 0-10s3-6 0-8M24 26c-3-4 3-6 0-10s3-6 0-8" fill="none" stroke="#f4ede4" stroke-width="1.6"/><line x1="7" y1="29" x2="29" y2="7" stroke="#f4ede4" stroke-width="1.8"/></svg>
      <p>ODOR<br>FREE</p>
    </div>

    <div class="band"></div>

    <div class="purity">
      <p class="natural">100% NATURAL</p>
      <p class="organic">100% organic</p>
    </div>

    <div class="brand-mark">
      <div class="dot"></div>
      <p class="name">Brindle Barks<br>Chews</p>
    </div>

    <p class="ingredient-count">ONLY<b>3</b>INGREDIENTS</p>
    <svg class="ingredient-arrow" width="30" height="66" viewBox="0 0 30 66" aria-hidden="true"><path d="M4 2v22M4 42v22M4 2l22 31L4 64" fill="none" stroke="#f4ede4" stroke-width="2"/></svg>

    <ul class="ingredients">
      <li>Yak Milk</li>
      <li>Lime Juice</li>
      <li>Himalayan Salt</li>
    </ul>

    <p class="net-weight">NET WT 200 g / 5 PCS</p>
  </section>
</main>
</body>
</html>
```